Business Card Design Project

Business Card
We are rebranding with a new logo
Industry/Entity Type
Business
Contact Information for Business Card
Dennis Morvale +61 487215963 dennis@quorv.com.au P.O. Box 872 Fernlow QLD 4309
Requirements
Must have
- Logo

```html
<!DOCTYPE html>
<html lang="en">
<head>
<meta charset="utf-8">
<title>Quorv International – Business Card</title>
<link rel="stylesheet" href="https://fonts.googleapis.com/css2?family=Open+Sans:wght@400;600;700&display=swap">
<style>
  :root {
    --backdrop: #2a2a2a;
    --card-white: #f4f4f4;
    --band-light: #0a9bd2;
    --band-deep: #0b5a82;
    --brand-blue: #0b6c98;
    --icon-blue: #0a85bf;
    --text-grey: #4a4a4a;
  }
  * { margin: 0; padding: 0; box-sizing: border-box; }
  html, body {
    width: 1200px;
    height: 915px;
    overflow: hidden;
    background: var(--backdrop);
    font-family: "Open Sans", sans-serif;
  }
  .card {
    position: absolute;
    left: 60px;
    top: 152px;
    width: 1080px;
    height: 610px;
    background: var(--card-white);
    overflow: hidden;
  }
  .header-band {
    position: absolute;
    left: 0;
    top: 0;
    width: 1080px;
    height: 200px;
    background: linear-gradient(90deg, var(--band-deep) 0%, var(--band-light) 70%, var(--band-deep) 100%);
  }
  .holder-name {
    position: absolute;
    right: 48px;
    top: 70px;
    color: #ffffff;
    font-weight: 700;
    font-size: 29px;
    letter-spacing: 0.5px;
    text-transform: uppercase;
  }
  .brand-name {
    position: absolute;
    left: 56px;
    top: 300px;
    color: var(--brand-blue);
    font-weight: 600;
    font-size: 50px;
    line-height: 1.05;
  }
  .contact-list {
    position: absolute;
    left: 56px;
    top: 462px;
    list-style: none;
    color: var(--text-grey);
    font-size: 26px;
    line-height: 34.5px;
  }
  .contact-list li { display: flex; align-items: center; }
  .contact-icon {
    width: 22px;
    height: 22px;
    margin-right: 17px;
    fill: var(--icon-blue);
    flex: none;
  }
  .postal-address {
    position: absolute;
    right: 48px;
    top: 503px;
    color: var(--text-grey);
    font-size: 26px;
    line-height: 35px;
    text-align: right;
    font-style: normal;
  }
</style>
</head>
<body>
  <div class="card">
    <div class="header-band" role="img" aria-label="Decorative blue and orange wave band"></div>

    <div class="holder-name">Dennis Morvale</div>

    <div class="brand-name">Quorv<br>International</div>

    <ul class="contact-list">
      <li>
        <svg class="contact-icon" viewBox="0 0 24 24" aria-hidden="true"><path d="M3 7c0-2 2-3 9-3s9 1 9 3v2h-5V7.5h-8V9H3z M6 11h12l3 8H3z"/></svg>
        +61 487215963
      </li>
      <li>
        <svg class="contact-icon" viewBox="0 0 24 24" aria-hidden="true"><path d="M2 6h20v2l-10 6L2 8z M2 10l10 6 10-6v8H2z"/></svg>
        dennis@quorv.com.au
      </li>
      <li>
        <svg class="contact-icon" viewBox="0 0 24 24" aria-hidden="true"><circle cx="12" cy="12" r="10"/></svg>
        www.quorv.com.au
      </li>
    </ul>

    <address class="postal-address">
      P.O. Box 872<br>
      Fernlow QLD 4309
    </address>
  </div>
</body>
</html>
```